Book Cover for Lantern Cousins Notes from the Orchard

We have written a book that brings together Notes from the Orchard from a variety of women's voices.
We developed a draft book cover that we like using Canva (attached below). We'd love a book cover that is similar to this image, but looks more professional.
Following are the themes we’d like to depict in the book cover, and in parentheses, how they are represented in the current cover:
1. Divinely feminine (overall cover)
2. Currents of enlightenment (the swirls of light carrying the butterfly)
3. Diversity (a myriad of colors)
4. The solo journey into the unknown (the single butterfly’s flight)
5. Buoyancy and joy (again, the dancing colors and floating butterfly)
6. Boldly feminine (the blue butterfly, set against brush strokes of light)
7. Homage to a dear friend (she loved blue butterflies, the cosmos - this butterfly has hints of the cosmos in her wings, and painting - this background has brush strokes of light).
Book Title, Subtitle, and Editor:
Lantern Cousins
Notes from the Orchard
Edited by Ilse Varno
Thank you very much for considering this project!
People who are interested in Women and Spirituality

```html
<!DOCTYPE html>
<html lang="en">
<head>
<meta charset="utf-8">
<title>Lantern Cousins — Notes from the Orchard</title>
<link rel="stylesheet" href="https://fonts.googleapis.com/css2?family=Cinzel:wght@400;500&family=Great+Vibes&display=swap">
<style>
  :root {
    --navy: #141c8a;
    --plum: #a6138b;
    --peach: #f6b8a0;
    --peach-deep: #f3a98c;
    --apricot: #f7c89a;
    --blush: #f9d9df;
    --pink: #f7c4e4;
    --cream: #fbe6e6;
    --wing-dark: #10124f;
    --wing-mid: #1a2a9a;
    --wing-light: #2fb6ea;
  }
  * { margin: 0; padding: 0; box-sizing: border-box; }
  html, body { width: 752px; height: 1200px; overflow: hidden; }
  body { background: var(--cream); }
  .cover {
    position: relative;
    width: 752px;
    height: 1200px;
    overflow: hidden;
    background:
      radial-gradient(ellipse 120px 200px at 10px 60px, var(--apricot) 0%, transparent 100%),
      radial-gradient(ellipse 360px 520px at 120px 620px, var(--peach-deep) 0%, transparent 100%),
      radial-gradient(ellipse 320px 520px at 640px 560px, var(--pink) 0%, transparent 100%),
      radial-gradient(ellipse 380px 300px at 520px 1120px, var(--cream) 0%, transparent 100%),
      linear-gradient(100deg, var(--peach) 0%, var(--blush) 50%, var(--pink) 100%);
  }
  .editor {
    position: absolute;
    top: 48px;
    left: 0;
    width: 100%;
    text-align: center;
    font-family: "Cinzel", serif;
    font-weight: 500;
    font-size: 27px;
    letter-spacing: 0.33em;
    padding-left: 0.33em;
    color: var(--navy);
  }
  .series {
    position: absolute;
    top: 88px;
    left: 0;
    width: 100%;
    text-align: center;
    font-family: "Cinzel", serif;
    font-weight: 400;
    font-size: 52px;
    letter-spacing: 0.26em;
    padding-left: 0.26em;
    color: var(--navy);
  }
  .title {
    position: absolute;
    top: 250px;
    left: 0;
    width: 100%;
    color: var(--plum);
    font-family: "Cinzel", serif;
    font-weight: 400;
    text-align: center;
  }
  .title-line {
    display: block;
    font-size: 92px;
    line-height: 96px;
    white-space: nowrap;
  }
  .title-line.first { letter-spacing: 0.22em; }
  .title-line.second { letter-spacing: 0.36em; padding-left: 0.36em; margin-top: 0; }
  .title-script {
    font-family: "Great Vibes", cursive;
    font-size: 64px;
    letter-spacing: 0;
    margin-left: -0.1em;
  }
  .butterfly {
    position: absolute;
    left: 98px;
    top: 600px;
    width: 525px;
    height: 373px;
    border-radius: 46% 46% 40% 40% / 40% 40% 56% 56%;
    background:
      radial-gradient(ellipse 160px 120px at 30% 78%, var(--wing-light) 0%, transparent 100%),
      radial-gradient(ellipse 160px 120px at 70% 78%, var(--wing-light) 0%, transparent 100%),
      linear-gradient(180deg, var(--wing-dark) 0%, var(--wing-mid) 60%, var(--wing-dark) 100%);
  }
</style>
</head>
<body>
  <main class="cover">
    <p class="editor">Edited by Ilse Varno</p>
    <p class="series">Lantern Cousins</p>
    <h1 class="title">
      <span class="title-line first">NOTES <span class="title-script">from the</span></span>
      <span class="title-line second">ORCHARD</span>
    </h1>
    <div class="butterfly" role="img" aria-label="A single deep blue butterfly with bright turquoise markings, wings open, floating on the painted background"></div>
  </main>
</body>
</html>
```